Agrarhandel benötigt Homepage
Zielgruppe
Wir sind ein Agrarhandel mit einem Warenumschlagslager im Sinne eines klassischen Einzelhandels und vertreiben Produkte an Landwirte.
Wir vertreiben folgende Hauptproduktgruppen:
Einzelfuttermittel
wie z.B. Sojaexktraktionsschrot. Die einzelnen Produkte könnten z.B. wie die Futtermittel auf folgender Seite dargestellt werden (https://www.kornprobe-beispiel.eu/de/produkt/trelomixan)
Mischfuttermittel
Hier bieten wir unseren Kunden an, individuelles Mischfutter auf Basis unserer Einzelfuttermittel herzustellen.
Weitere Details und weitere Produktbereiche habe ich in einer Powerpoint-Übersicht dargestellt.
Neben diesen Produkten wollen wir uns als Familienunternehmen selbst vorstellen. Zudem betreiben wir in unserer Familie zusätzlich einen Milchviehbetrieb den wir ebenfalls hervorheben möchten, da wir unseren Kunden gegenüber einerseits als Zulieferer aber auch als Kollege auftreten wollen.
Einzelfuttermittel: Hier können wir durch unsere Unabhängigkeit punkten, da wir nicht abhängig von bestimmten Lieferanten sind und dementsprechend unabhängig beraten können. Wir untersuchen im Vergleich zu unseren Wettbewerben die Qualität der Futtermittel bis ins Detail und können daher eine Transparenz bieten, die Konkurrenten in der Regel nicht bieten können. Unser Warenumschlagsplatz mit moderner Technik ermöglicht es uns äußerst kosteneffizient die Waren umschlagen und ausliefern zu können.
Mischfuttermittel: Auf Basis der vorhandenen Einzelfuttermittel stellen wir je nach Kundenwunsch individuelle Mischfutter her. Wir arbeiten mit offenen Deklarationen, sodass unsere Kunden jederzeit nachvollziehen können, ob auch die Einzelfuttermittel verwendet wurden, die sie bestellt haben und keine billigen Ersatzprodukte verwendet wurden.
Zudem sind wir BT und HUPA zertifiziert. Die aktuellen für unser Unternehmen ausgestellten Zertifikate müssen für unsere Kunden als Download zur Verfügung stehen. Statt dem HUPA-Logo bitte das ..
Aufgabenstellung
Wir möchten gerne ein zeitgemäße Homepage, jedoch muss auch berücksichtigt werden, dass unsere Kunden eher konservativ denken.

```html
<!DOCTYPE html>
<html lang="de">
<head>
<meta charset="utf-8">
<title>Lieferanten – Altmühl Agrarhandel</title>
<link href="https://fonts.googleapis.com/css2?family=Inter:wght@500;600;800&family=Josefin+Sans:wght@400;600&display=swap" rel="stylesheet">
<style>
:root{
  --green:#136a54;
  --orange:#f9ae26;
  --heading:#f6a927;
  --ink:#111;
  --white:#fff;
  --ui:'Josefin Sans', sans-serif;
  --text:'Inter', sans-serif;
}
*{margin:0;padding:0;box-sizing:border-box}
html,body{width:786px;height:1200px;overflow:hidden;background:var(--white)}
.page{position:relative;width:786px;height:1200px;font-family:var(--text);color:var(--ink)}
.site-header{position:absolute;left:0;top:0;width:786px;height:75px;background:var(--green)}
.header-accent{position:absolute;left:0;top:0;width:46px;height:75px;background:var(--orange)}
.brand{position:absolute;left:46px;top:0;width:128px;height:75px;background:var(--white);display:flex;flex-direction:column;align-items:center;justify-content:center;gap:8px}
.brand-dot{width:24px;height:24px;border-radius:50%;background:var(--orange)}
.brand-name{font-family:var(--ui);font-weight:600;font-size:8.6px;color:var(--green);white-space:nowrap}
.main-nav{position:absolute;top:35px;left:284px;width:444px;display:flex;justify-content:space-between;font-family:var(--ui);font-weight:600;font-size:9.6px;color:var(--white);white-space:nowrap}
.main-nav .active{color:var(--orange)}
.search-icon{position:absolute;left:745px;top:33px}
.hero{position:absolute;left:0;top:88px;width:786px;height:234px;background:linear-gradient(180deg,#c9b57a 0%,#cf9a45 30%,#b8782e 70%,#a96c2a 100%)}
.hero-title{position:absolute;left:318px;top:174px;width:146px;height:45px;border-radius:12px;background:rgba(150,100,60,.55);border-bottom:1.5px solid #f3e6d4;font-weight:500;font-size:22px;display:flex;align-items:center;justify-content:center;color:#111}
.gallery-photo{position:absolute;top:270px;width:147px;height:100px}
.photo-grass{left:162px;background:linear-gradient(160deg,#f1d58a 0%,#9aa44a 45%,#3f5a1f 100%)}
.photo-wheat{left:318px;background:linear-gradient(160deg,#d99a3c 0%,#eab364 45%,#b8741f 100%)}
.photo-harvest{left:473px;background:linear-gradient(170deg,#e6a357 0%,#b57536 45%,#7d5028 100%)}
.content h2{position:absolute;font-weight:800;font-size:19.5px;color:var(--heading);white-space:nowrap}
.content p{position:absolute;left:164px;font-weight:500;font-size:13.2px;line-height:15.8px}
.band{position:absolute;left:0;width:786px;background:var(--orange)}
.footer-col{position:absolute;top:987px;font-family:var(--ui);font-size:10.6px;line-height:18.6px;color:var(--green);white-space:nowrap}
.footer-col .label{color:var(--orange)}
.contact-line{display:flex;align-items:center;gap:5px}
.badge{position:absolute;top:1015px;border-radius:3px}
.badge-green{left:679px;width:43px;height:43px;background:#5bb432;border:2px solid #d9ecd0}
.badge-blue{left:730px;width:36px;height:40px;background:#fff;border:1.5px solid #2a7fc4}
.terms{position:absolute;left:0;top:1096px;width:786px;text-align:center;font-family:var(--ui);font-size:10.5px;line-height:18.6px;color:#222;white-space:nowrap}
.copyright{position:absolute;left:0;top:1180px;width:786px;text-align:center;font-size:7px;font-weight:600;color:#3a2a10}
</style>
</head>
<body>
<div class="page">
  <header class="site-header">
    <div class="header-accent"></div>
    <div class="brand"><span class="brand-dot"></span><span class="brand-name">ALTMÜHL AGRARHANDEL</span></div>
    <nav class="main-nav">
      <span class="active">LANDWIRT</span><span>GESCHÄFTSPARTNER</span><span>LIEFERANTEN</span><span>PRODUKTE ⌄</span><span>FIRMENPRÄSENTATION</span>
    </nav>
    <svg class="search-icon" width="14" height="14" viewBox="0 0 14 14" fill="none" stroke="#fff" stroke-width="1.5"><circle cx="5.5" cy="5.5" r="4.5"/><line x1="9" y1="9" x2="13.5" y2="13.5"/></svg>
  </header>

  <section class="hero" role="img" aria-label="Strohballen auf einem Feld vor hügeliger Landschaft"></section>
  <div class="hero-title">Lieferanten</div>
  <div class="gallery-photo photo-grass" role="img" aria-label="Getreidehalm im Gegenlicht der Sonne"></div>
  <div class="gallery-photo photo-wheat" role="img" aria-label="Reife Weizenähren"></div>
  <div class="gallery-photo photo-harvest" role="img" aria-label="Mähdrescher bei der Ernte"></div>

  <main class="content">
    <h2 style="left:160px;top:418px">Lorem ipsum dolor sit amet</h2>
    <p style="top:462px;width:450px">Ut enim ad minim veniam, quis nostrud exercitation ullamco laboris nisi ut aliquip ex ea Ut enim ad minim veniam, quis nostrud exercitation ullamco laboris nisi ut aliquip ex ea commodo coUt enim ad minim veniam, quis nostrud exercitation ullamco laboris nisi ut aliquip ex ea commodo co con.</p>
    <h2 style="left:166px;top:570px">Duis aute irure dolor in reprehenderit</h2>
    <p style="top:614px;width:450px">Ut enim ad minim veniam, quis nostrud exercitation ullamco laboris nisi ut aliquip ex ea Ut enim ad minim veniam, quis nostrud exercitation ullamco laboris nisi ut aliquip ex ea commodo coUt enim ad minim veniam, quis nostrud exercitation ullamco laboris nisi ut aliquip ex ea commodo co con.</p>
    <h2 style="left:170px;top:733px">Nemo enim ipsam voluptatem quia</h2>
    <p style="top:777px;width:510px">Lorem ipsum dolor sit amet, consectetur adipiscing elit, sed do eiusmod tempor incididunt ut labore Lorem ipsum dolor sit amet, consectetur adipiscing elit, sed do eiusmod tempor incididunt ut labore Lorem ipsum dolor sit amet, consectetur adipiscing elit, sed do eiusmod tempor incididunt ut labore</p>
  </main>

  <div class="band" style="top:933px;height:33px"></div>

  <footer>
    <div class="footer-col" style="left:23px"><div class="label">Postanschrift</div>Altmühl Agrarhandel GbR<br>Lindenweg 7<br>92341 Eichenried</div>
    <div class="footer-col" style="left:156px"><div class="label">Lieferanschrift</div>Altmühl Agrarhandel GbR<br>Mühlgasse 3<br>92341 Eichenried</div>
    <div class="footer-col" style="left:292px;top:988px">
      <div class="contact-line"><svg width="11" height="11" viewBox="0 0 12 12"><circle cx="6" cy="6" r="6" fill="var(--orange)"/><path d="M4 3l1.2 1.6-.7.8a4 4 0 002.1 2.1l.8-.7L9 8 8.2 9.2C5.8 9 3 6.2 2.8 3.8z" fill="#fff"/></svg>09123 45 67 80</div>
      <div class="contact-line"><svg width="11" height="11" viewBox="0 0 12 12"><rect x="3" y="1" width="6" height="10" rx="1.2" fill="var(--orange)"/></svg>0171 234 56 78</div>
      <div class="contact-line"><svg width="11" height="11" viewBox="0 0 12 12"><rect x="1" y="3" width="10" height="7" rx="1" fill="var(--orange)"/><path d="M1.5 3.5L6 7l4.5-3.5" stroke="#fff" fill="none"/></svg>Info@Altmuehl-Agrar.De</div>
      <div class="contact-line"><svg width="11" height="11" viewBox="0 0 12 12" fill="none" stroke="var(--orange)" stroke-width="1.2"><circle cx="6" cy="6" r="5"/><path d="M1 6h10M6 1c2 2 2 8 0 10M6 1c-2 2-2 8 0 10"/></svg>Www.Altmuehl-Agrar.De</div>
    </div>
    <div class="footer-col" style="left:468px;top:988px">Bankverbindung: Volksbank Talgrund<br>IBAN: DE12 3456 7890 1234 5678 90<br>BIC: GENODEF1XYZ<br>USt-IdNr.: DE123456789</div>
    <div class="badge badge-green" role="img" aria-label="Zertifizierungssiegel"></div>
    <div class="badge badge-blue" role="img" aria-label="Qualitätssiegel"></div>
    <p class="terms">Es Gelten Die Allgemeinen Lieferungs- Und Zahlungsbedingungen. Die Ware Bleibt Bis Zur Vollständigen Bezahlung<br>Unser Eigentum, Auch Bei Veräußerung, Verfütterung Oder Einer Weiteren Verwendung (Erweiterter Verlängerter Eigentumsvorbehalt).<br>Bei Verspäteter Zahlung Werden Übliche Verzugszinsen Berechnet. Gerichtsstand Ist Talheim I. D. Op</p>
    <div class="band" style="top:1168px;height:32px"></div>
    <div class="copyright">Copyright 2023 All Right Reserved</div>
  </footer>
</div>
</body>
</html>
```